A5 Flyer for Financial Services Business

I am after a re-design of our business flyer to fit in with our new branding style and logo colour scheme. Wanting something with a bit of designer flair that I could not create myself. I have included the flyer which I created which lacks style so dazzle me.

I want to use the same content.

Text for main body of flyer is

Are you a small business owner, tradie or TRPQ Service Provider struggling to stay on top of your bookkeeping and compliance obligations? If so we would love to help you get back on track and take control of your business finances so that you can make informed business decisions and focus on what you do best.

We have over 20 years industry experience and, as a small business ourselves, we are able to offer our clients a personal bookkeeping solution tailored to meet the needs of your business.

Accounts Payable | Accounts Receivable
Customer Invoicing
Bank and Credit Card Reconciliations
Payroll | Superannuation | Payroll Tax
Business Activity | Instalment Activity Statements
Regular Financial Reports
Vantly and Brimfolk Set-Up and Training

```html
<!DOCTYPE html>
<html lang="en">
<head>
<meta charset="utf-8">
<title>Even Keel Financial Services – Bookkeeping Flyer</title>
<link rel="stylesheet" href="https://fonts.googleapis.com/css2?family=Montserrat:wght@300;400;500&family=Rubik:wght@500;700;800&display=swap">
<style>
:root{
  --stage:#c9c9c9;
  --teal:#0f8f8e;
  --teal-deep:#0b5f6c;
  --mint:#19b3a1;
  --ink:#1e1e20;
  --body:#333336;
  --charcoal:#3a3a3d;
  --paper:#ffffff;
  --mist:#e4e5e7;
}
*{box-sizing:border-box;margin:0;padding:0}
html,body{width:1200px;height:2434px;overflow:hidden;background:var(--stage)}
.flyer{position:absolute;left:50px;top:438px;width:1100px;height:1558px;background:var(--paper);overflow:hidden;box-shadow:0 10px 30px rgba(0,0,0,.18)}
.flyer-art{position:absolute;inset:0;width:100%;height:100%}
.headline{position:absolute;left:647px;top:85px;font-family:"Rubik",sans-serif;font-weight:800;font-size:59px;line-height:66px;color:var(--paper)}
.services-title{position:absolute;left:576px;top:636px;font-family:"Rubik",sans-serif;font-weight:700;font-size:29px;color:var(--ink);white-space:nowrap}
.services-title em{font-style:normal;color:var(--mint)}
.services-rule{position:absolute;left:576px;top:682px;width:118px;height:4px;background:linear-gradient(90deg,var(--teal-deep) 60%,var(--mint) 60%)}
.service{position:absolute;display:flex;align-items:center;gap:14px;font-family:"Rubik",sans-serif;font-weight:500;font-size:22px;line-height:23px;color:var(--ink)}
.service svg{flex:none;width:36px;height:36px}
.brand{position:absolute;left:0;width:508px;text-align:center;font-family:"Montserrat",sans-serif;font-weight:300;color:var(--teal-deep)}
.brand-mark{position:absolute;left:216px;top:730px;width:76px;height:76px;border-radius:50%;background:var(--teal-deep)}
.brand-name{top:818px;font-size:40px;letter-spacing:1px}
.brand-sub{top:872px;font-size:20px;letter-spacing:9px;color:#6b6e72}
.intro{position:absolute;left:49px;width:418px;font-family:"Montserrat",sans-serif;font-weight:400;font-size:17.5px;line-height:22.3px;color:var(--body);text-align:justify}
.intro-a{top:923px}
.intro-b{top:1095px}
.phone{position:absolute;left:52px;top:1474px;display:flex;align-items:center;gap:12px;font-family:"Rubik",sans-serif;font-weight:500;font-size:48px;color:var(--paper)}
.web{position:absolute;left:528px;top:1500px;display:flex;align-items:center;gap:12px;font-family:"Rubik",sans-serif;font-weight:700;font-size:19px;color:var(--paper);white-space:nowrap}
.web-domain em{font-style:normal;color:var(--mint)}
</style>
</head>
<body>
<main class="flyer">
  <svg class="flyer-art" viewBox="0 0 745 1055" preserveAspectRatio="none">
    <defs>
      <linearGradient id="tealPanel" x1="0" y1="0" x2="1" y2="1">
        <stop offset="0" stop-color="#12a59c"/>
        <stop offset="1" stop-color="#0a5e6b"/>
      </linearGradient>
      <linearGradient id="greyPanel" x1="0" y1="0" x2="1" y2="1">
        <stop offset="0" stop-color="#d6d8db"/>
        <stop offset="1" stop-color="#f6f6f7"/>
      </linearGradient>
      <linearGradient id="silver" x1="0" y1="0" x2="1" y2="0">
        <stop offset="0" stop-color="#e9eaec"/>
        <stop offset="1" stop-color="#8d9096"/>
      </linearGradient>
      <linearGradient id="photoTop" x1="0" y1="0" x2="1" y2="1">
        <stop offset="0" stop-color="#8d9aa3"/>
        <stop offset=".55" stop-color="#6e5b4c"/>
        <stop offset="1" stop-color="#3e3a38"/>
      </linearGradient>
      <linearGradient id="photoTeam" x1="0" y1="0" x2="1" y2="1">
        <stop offset="0" stop-color="#c7ccd2"/>
        <stop offset=".6" stop-color="#9a7b68"/>
        <stop offset="1" stop-color="#2d3340"/>
      </linearGradient>
      <linearGradient id="tealBar" x1="0" y1="0" x2="1" y2="0">
        <stop offset="0" stop-color="#0a5f6c"/>
        <stop offset="1" stop-color="#119a95"/>
      </linearGradient>
    </defs>

    <polygon points="0,502 372,395 372,815 0,840" fill="url(#greyPanel)"/>
    <path d="M372,395 L372,815 Q372,838 350,838 L0,840 L0,835 L350,835 Q368,835 368,815 L368,396 Z" fill="#d2d4d7" opacity=".4"/>

    <polygon points="0,0 400,0 378,355 0,462" fill="url(#photoTop)" role="img" aria-label="Photo: woman in glasses working with a calculator and paperwork at an office desk"/>
    <polygon points="398,0 745,0 745,245 378,352" fill="url(#tealPanel)"/>
    <polygon points="378,352 745,245 745,266 405,362" fill="url(#silver)"/>
    <polygon points="0,462 378,352 405,362 0,500" fill="url(#tealBar)"/>

    <rect x="645" y="358" width="66" height="80" rx="6" fill="var(--teal)" opacity=".25" role="img" aria-label="Hummingbird illustration"/>

    <polygon points="385,985 440,800 635,768 745,768 745,985" fill="url(#photoTeam)" role="img" aria-label="Photo: three smiling colleagues meeting around a table with documents"/>
    <polygon points="700,768 745,742 745,790" fill="var(--teal)"/>
    <polygon points="385,985 415,890 425,895 398,985" fill="var(--teal)"/>

    <g role="img" aria-label="Partner and registration badges">
      <circle cx="65" cy="902" r="31" fill="#eef0e6" stroke="#bfc3c7" stroke-width="1"/>
      <circle cx="143" cy="912" r="32" fill="#1bb1e0"/>
      <circle cx="213" cy="912" r="32" fill="#0f7b8c"/>
      <rect x="270" y="872" width="66" height="66" rx="4" fill="#eef1ef" stroke="#d9ddd9"/>
    </g>
    <text x="65" y="948" font-family="Montserrat, sans-serif" font-size="6.5" text-anchor="middle" fill="#333">BAS agent</text>
    <text x="65" y="956" font-family="Montserrat, sans-serif" font-size="6.5" text-anchor="middle" fill="#333">20481137</text>

    <polygon points="300,995 745,995 745,1055 340,1055" fill="var(--charcoal)"/>
    <polygon points="0,985 300,985 340,1055 0,1055" fill="url(#tealBar)"/>
    <polygon points="300,985 312,985 352,1055 340,1055" fill="#ffffff"/>
  </svg>

  <h1 class="headline">Bookkeeping<br>tailored to<br>your business<br>needs</h1>

  <h2 class="services-title">Bookkeeping <em>Services</em> include</h2>
  <div class="services-rule"></div>

  <div class="service" style="left:578px;top:716px"><svg viewBox="0 0 36 36"><rect x="4" y="16" width="12" height="16" rx="2" fill="var(--teal)"/><path d="M10 14V4M6 8l4-4 4 4" stroke="var(--teal)" stroke-width="3" fill="none"/><circle cx="25" cy="24" r="8" fill="var(--teal)"/></svg>Accounts<br>Receivable</div>
  <div class="service" style="left:578px;top:795px"><svg viewBox="0 0 36 36"><rect x="6" y="3" width="22" height="30" rx="3" fill="var(--teal)"/><path d="M11 12h12M11 18h12M11 24h8" stroke="#fff" stroke-width="2.5"/></svg>Business<br>Activity</div>
  <div class="service" style="left:578px;top:873px"><svg viewBox="0 0 36 36"><circle cx="18" cy="13" r="10" fill="var(--teal)"/><path d="M4 28q8-6 14 0t14-2" stroke="var(--teal)" stroke-width="3" fill="none"/></svg>Accounts<br>Payable</div>
  <div class="service" style="left:578px;top:951px"><svg viewBox="0 0 36 36"><rect x="5" y="4" width="26" height="28" rx="2" fill="var(--teal)"/><path d="M10 11h16M10 17h16M10 23h16" stroke="#fff" stroke-width="2"/></svg>Customer<br>Invoicing</div>
  <div class="service" style="left:578px;top:1030px"><svg viewBox="0 0 36 36"><rect x="6" y="3" width="24" height="22" rx="2" fill="var(--teal)"/><path d="M3 24l15 10 15-10" stroke="var(--teal)" stroke-width="3" fill="none"/></svg>Payroll/<br>Payroll Tax</div>

  <div class="service" style="left:786px;top:716px"><svg viewBox="0 0 36 36"><rect x="6" y="3" width="24" height="30" rx="3" fill="var(--teal)"/><path d="M12 27v-6M18 27v-10M24 27v-14" stroke="#fff" stroke-width="3"/></svg>Regular Financial<br>Reports</div>
  <div class="service" style="left:786px;top:795px"><svg viewBox="0 0 36 36"><rect x="3" y="9" width="28" height="18" rx="3" fill="var(--teal)"/><rect x="3" y="13" width="28" height="4" fill="#fff"/></svg>Bank and Credit<br>Card Reconciliations</div>
  <div class="service" style="left:786px;top:873px"><svg viewBox="0 0 36 36"><rect x="9" y="3" width="22" height="30" rx="2" fill="var(--teal)"/><rect x="4" y="8" width="5" height="20" fill="var(--teal)"/><path d="M14 11h12M14 17h12M14 23h12" stroke="#fff" stroke-width="2"/></svg>Instalment Activity<br>Statements</div>
  <div class="service" style="left:786px;top:951px"><svg viewBox="0 0 36 36"><circle cx="9" cy="9" r="5" fill="var(--teal)"/><path d="M4 32V18h10v14" fill="var(--teal)"/><rect x="17" y="5" width="16" height="14" fill="var(--teal)"/></svg>Vantly and Brimfolk<br>Set-Up and Training</div>
  <div class="service" style="left:786px;top:1036px"><svg viewBox="0 0 36 36"><rect x="3" y="20" width="30" height="12" rx="3" fill="var(--teal)"/><path d="M10 17V5M6 9l4-4 4 4M24 17V5M20 9l4-4 4 4" stroke="var(--teal)" stroke-width="3" fill="none"/></svg>Superannuation</div>

  <div class="brand-mark"></div>
  <div class="brand brand-name">EVEN KEEL</div>
  <div class="brand brand-sub">Financial Services</div>

  <p class="intro intro-a">Are you a small business owner, tradie or TRPQ Service Provider struggling to stay on top of your bookkeeping and compliance obligations? If so we would love to help you get back on track and take control of your business finances so that you can make informed business decisions and focus on what you do best.</p>
  <p class="intro intro-b">We have over 20 years industry experience and, as a small business ourselves, we are able to offer our clients a personal bookkeeping solution tailored to meet the needs of your business.</p>

  <div class="phone"><svg width="22" height="22" viewBox="0 0 22 22"><circle cx="11" cy="11" r="11" fill="#fff"/><path d="M7 6c1-1 2 0 3 2s-1 2 0 3 2 2 3 1 2 1 2 2-2 3-5 1-5-5-3-9z" fill="var(--teal-deep)"/></svg>0400 555 018</div>
  <div class="web"><svg width="18" height="18" viewBox="0 0 18 18"><circle cx="9" cy="9" r="8" fill="none" stroke="var(--mint)" stroke-width="2"/><path d="M1 9h16M9 1v16" stroke="var(--mint)" stroke-width="1.5"/></svg><span class="web-domain">www.<em>evenkeelfinancialservices</em>.com.au</span></div>
</main>
</body>
</html>
```